​Silver Harbor Rhythm provides personal, friendly service in a fun and high energy environment. We are based in Vermont.

We would like a card that appeals to a wide range of audiences as we do a wide range of events. Please feel free to check out our website silverharborrhythm.net for inspiration.

Target Market(s)

weddings, corporate, birthday parties, colleges

Industry/Entity Type

Business

Contact Information for Business Card

Silver Harbor Rhythm
Providing Entertainment For All Occasions
555 274 9160
silverharborrhythm@mailnest.net
silverharborrhythm.net

```html
<!DOCTYPE html>
<html lang="en">
<head>
<meta charset="UTF-8">
<title>Silver Harbor Rhythm – Business Cards</title>
<link href="https://fonts.googleapis.com/css2?family=Open+Sans:wght@400;600;700&display=swap" rel="stylesheet">
<style>
  :root {
    --backdrop: #ece9e4;
    --card: #ffffff;
    --green: #2f6a1c;
    --green-dark: #245215;
    --red: #7e0f12;
    --ink: #3a3a3a;
    --ink-soft: #555555;
  }
  * { margin: 0; padding: 0; box-sizing: border-box; }
  html, body {
    width: 1200px; height: 829px; overflow: hidden;
    background: var(--backdrop);
    font-family: "Open Sans", Arial, sans-serif;
  }
  .stage {
    position: relative; width: 1200px; height: 829px;
    display: flex; align-items: center; justify-content: center; gap: 60px;
  }
  .card {
    position: relative; width: 520px; height: 298px;
    background: var(--card);
    box-shadow: 0 6px 18px rgba(0,0,0,0.18);
    overflow: hidden;
  }

  /* Contact side */
  .brand-mark {
    position: absolute; top: 26px; right: 28px;
    display: flex; align-items: center; gap: 8px;
    color: var(--green); font-weight: 700; font-size: 17px;
  }
  .brand-mark .dot { width: 12px; height: 12px; background: var(--red); }
  .identity {
    position: absolute; top: 102px; left: 0;
    padding-left: 30px; border-left: 8px solid var(--red);
    margin-left: 16px;
  }
  .identity .name { color: var(--green); font-weight: 700; font-size: 17px; line-height: 1.2; }
  .identity .title { color: var(--ink); font-weight: 600; font-size: 12px; }
  .contacts {
    position: absolute; top: 160px; left: 46px;
    list-style: none; font-size: 12.5px; color: var(--ink);
  }
  .contacts li { display: flex; align-items: center; gap: 8px; line-height: 20px; }
  .contacts svg { width: 12px; height: 12px; flex: none; }
  .address { position: absolute; top: 232px; left: 46px; font-size: 12.5px; color: var(--ink); }
  .band-green {
    position: absolute; left: 0; top: 262px; width: 410px; height: 16px;
    background: var(--green);
  }
  .band-red-block {
    position: absolute; right: 0; top: 246px; width: 100px; height: 16px;
    background: var(--red);
  }
  .band-red-line {
    position: absolute; left: 0; right: 0; bottom: 0; height: 6px;
    background: var(--red);
  }

  /* Logo side */
  .logo-side {
    display: flex; flex-direction: column; align-items: center; justify-content: center; gap: 34px;
  }
  .logo-side .brand-mark {
    position: static; font-size: 32px; gap: 14px;
  }
  .logo-side .brand-mark .dot { width: 20px; height: 20px; }
  .website { font-size: 18px; color: var(--ink-soft); letter-spacing: 0.5px; }
</style>
</head>
<body>
<main class="stage">
  <section class="card contact-side">
    <div class="brand-mark"><span class="dot"></span>Silver Harbor Rhythm</div>
    <div class="identity">
      <p class="name">Your Name</p>
      <p class="title">Title</p>
    </div>
    <ul class="contacts">
      <li>
        <svg viewBox="0 0 12 12"><path d="M3 1 L5 3.5 L4 5 Q5 7 7 8 L8.5 7 L11 9 L10 11 Q4 11 1 4 Z" fill="var(--green)"/></svg>
        555 274 9160
      </li>
      <li>
        <svg viewBox="0 0 12 12"><rect x="1" y="2.5" width="10" height="7" fill="var(--green)"/><path d="M1 2.5 L6 6.5 L11 2.5" stroke="#fff" fill="none"/></svg>
        silverharborrhythm@mailnest.net
      </li>
      <li>
        <svg viewBox="0 0 12 12"><circle cx="6" cy="6" r="5" fill="none" stroke="var(--green)" stroke-width="1.4"/><path d="M1 6 H11 M6 1 Q3 6 6 11 M6 1 Q9 6 6 11" stroke="var(--green)" fill="none"/></svg>
        www.silverharborrhythm.net
      </li>
    </ul>
    <p class="address">Street Name, City Name, Zip Code:00000</p>
    <div class="band-red-block"></div>
    <div class="band-green"></div>
    <div class="band-red-line"></div>
  </section>

  <section class="card logo-side">
    <div class="brand-mark"><span class="dot"></span>Silver Harbor Rhythm</div>
    <p class="website">www.silverharborrhythm.net</p>
  </section>
</main>
</body>
</html>
```